Wix Design for a Clothing Design Web Marketing Site

We need a Wix design and content (including any images and copy) for a clothing design web storefront, Sew To Suit (or sewtosuit). Rough ideas and content can be found at http://marenvoltis.wix.com/sewtosuit.

Sew To Suit is an innovative business concept that combines fashion and entertainment. The business model allows customers to actively participate in the creation of fashion designs/concepts , visualize the garment in the customer’s body in 3D, and buy the physical garment made specially to fit the customer.
The fashion consultant will be able to create the design based on client's desires and test various possibilities (size, fabric, cut, etc..) in front of the customer, using software Drapova (the software is a key component of this business model)
(when developing the website use images from Drapova)
After the design is created, the customer can choose to order the actual piece. The garment will be made according to the created design, the customer measurements.

Target Market(s)

Primarily women from 25 to 45, who are fashion enthusiasts and appreciate fit and exclusivity. They are hedonistic shoppers, who shop for entertainment.
Men (metrosexuals) who are fashion enthusiasts, also hedonistic shoppers.

Industry/Entity Type

Clothing

Font styles to use
Serif
Sans Serif

Requirements
Must have
• Must have a landing page (home) or section, that gives the consumer an idea of what Sew To Suit will do for them, an about page or section that tells about the company and product, a how it works page or section that describes how it works (http://marenvoltis.wix.com/sewtosuit#!services3/c192y), and page or section about pricing, and a page or section on how to contact us.
Nice to have
• Very modern and clean. The website must be based on the main picture of the studio in the example. If that studio is the store, what will the website look like?
• Colors yellow, grey and white. Use the zig zag in yellow and white. You can change the size of the lines. The zig zagi gives the modern and bold accent. Outfits in pictures must show nicely tailored garments.

```html
<!DOCTYPE html>
<html lang="en">
<head>
<meta charset="utf-8">
<title>Sew To Suit</title>
<link rel="stylesheet" href="https://fonts.googleapis.com/css2?family=Lora:ital,wght@0,400;0,700;1,400;1,700&display=swap">
<style>
  :root {
    --black: #000000;
    --panel: #59585a;
    --yellow: #f5f20f;
    --white: #ffffff;
    --soft: #e9e6e0;
    --sepia-light: #e8dcc8;
    --sepia-mid: #a88f6c;
    --sepia-dark: #4a3a28;
    --rule: #2a2a2a;
  }
  * { box-sizing: border-box; margin: 0; padding: 0; }
  html, body { width: 965px; height: 1200px; overflow: hidden; background: var(--black); }
  body { font-family: "Lora", Georgia, serif; color: var(--white); position: relative; }

  .site-header { position: absolute; left: 0; top: 0; width: 965px; height: 195px; background: var(--black); }
  .brand-frame {
    position: absolute; left: 414px; top: 17px; width: 137px; height: 109px;
    border: 1px solid var(--soft);
    display: flex; flex-direction: column; align-items: center; justify-content: center; gap: 10px;
  }
  .brand-mark { width: 18px; height: 18px; background: var(--yellow); }
  .brand-name { font-size: 17px; font-weight: 700; color: var(--yellow); }

  .main-nav { position: absolute; top: 154px; left: 0; width: 965px; display: flex; justify-content: center; }
  .main-nav a {
    font-size: 10.5px; font-weight: 700; letter-spacing: 0.2px; color: var(--white);
    text-decoration: none; padding: 2px 14px; line-height: 14px;
    border-left: 1px solid var(--white);
  }
  .main-nav a:first-child { border-left: none; }
  .main-nav a.is-current { color: var(--yellow); }

  .edge { position: absolute; left: 0; width: 965px; height: 6px; }
  .edge-top { top: 192px; }
  .edge-bottom { top: 999px; }

  .hero { position: absolute; left: 0; top: 195px; width: 965px; height: 318px; }
  .photo {
    position: absolute;
    background: radial-gradient(ellipse at 40% 45%, var(--sepia-light) 0%, var(--sepia-mid) 55%, var(--sepia-dark) 100%);
  }
  .hero-photo { left: 0; top: 0; width: 482px; height: 318px; }
  .hero-panel { position: absolute; left: 482px; top: 0; width: 483px; height: 318px; background: var(--panel); }
  .notch { position: absolute; }
  .hero-notch { left: 446px; top: 141px; }
  .hero-welcome { position: absolute; left: 37px; top: 46px; font-size: 40px; font-weight: 400; letter-spacing: 0.5px; line-height: 48px; }
  .hero-title { position: absolute; left: 37px; top: 94px; font-size: 50px; font-weight: 700; font-style: italic; line-height: 60px; }
  .hero-tagline { position: absolute; left: 37px; top: 166px; font-size: 18px; font-style: italic; color: var(--soft); }
  .read-more {
    position: absolute; left: 36px; top: 227px; width: 130px; height: 35px;
    background: var(--black); border: 1px solid var(--yellow); border-radius: 2px;
    color: var(--yellow); font-size: 12.5px; font-weight: 700; text-decoration: none;
    display: flex; align-items: center; justify-content: center;
  }

  .process { position: absolute; left: 0; top: 513px; width: 965px; height: 489px; }
  .process-panel { position: absolute; left: 0; top: 0; width: 482px; height: 489px; background: var(--panel); }
  .process-photo { left: 482px; top: 0; width: 483px; height: 489px;
    background: radial-gradient(ellipse at 55% 40%, var(--sepia-light) 0%, var(--sepia-mid) 55%, var(--sepia-dark) 100%); }
  .process-notch { left: 482px; top: 199px; }
  .steps { position: absolute; left: 81px; top: 30px; list-style: none; width: 300px; }
  .step h2 { font-size: 18px; font-weight: 700; line-height: 24px; }
  .step p { font-size: 10.5px; line-height: 23px; color: var(--soft); }
  .step { height: 84px; }
  .step.short { height: 57px; }

  .site-footer { position: absolute; left: 0; top: 1002px; width: 965px; height: 198px; background: var(--black); }
  .footer-brand { position: absolute; left: 79px; top: 28px; width: 123px; height: 91px; display: flex; align-items: center; gap: 8px; }
  .footer-brand .brand-mark { width: 14px; height: 14px; }
  .footer-brand .brand-name { font-size: 17px; }
  .footer-nav { position: absolute; left: 222px; top: 69px; display: flex; }
  .footer-nav a { font-size: 10.5px; color: var(--white); text-decoration: none; padding: 0 10px; line-height: 13px; border-left: 1px solid var(--white); }
  .footer-nav a:first-child { padding-left: 0; border-left: none; }
  .contact { position: absolute; right: 79px; top: 40px; list-style: none; text-align: right; }
  .contact li { font-size: 10.5px; line-height: 21.5px; display: flex; justify-content: flex-end; align-items: center; gap: 7px; }
  .contact svg { fill: var(--yellow); }
  .footer-rule { position: absolute; left: 0; top: 149px; width: 965px; height: 1px; background: var(--rule); }
  .copyright { position: absolute; left: 0; top: 166px; width: 965px; text-align: center; font-size: 10.5px; }
  .social { position: absolute; left: 806px; top: 168px; display: flex; gap: 9px; }
  .social span { width: 14px; height: 14px; background: var(--white); border-radius: 50%; }
</style>
</head>
<body>
<svg width="0" height="0" style="position:absolute">
  <defs>
    <pattern id="saw" width="6" height="6" patternUnits="userSpaceOnUse">
      <path d="M0 6 L3 1 L6 6 Z" fill="#59585a"/>
    </pattern>
    <pattern id="saw-down" width="6" height="6" patternUnits="userSpaceOnUse">
      <path d="M0 0 L3 5 L6 0 Z" fill="#59585a"/>
    </pattern>
  </defs>
</svg>

<header class="site-header">
  <div class="brand-frame">
    <span class="brand-mark"></span>
    <span class="brand-name">Sew To Suit</span>
  </div>
  <nav class="main-nav">
    <a class="is-current" href="#">HOME</a>
    <a href="#">WHAT IS SEW TO SUIT?</a>
    <a href="#">HOW IS WORKS</a>
    <a href="#">PRICE</a>
    <a href="#">CONTACT US</a>
  </nav>
</header>

<svg class="edge edge-top" viewBox="0 0 965 6"><rect width="965" height="6" fill="url(#saw)"/></svg>

<section class="hero">
  <div class="photo hero-photo" role="img" aria-label="Sepia fashion photo of a couple in summer outfits and sunglasses"></div>
  <div class="hero-panel">
    <p class="hero-welcome">Welcome to</p>
    <h1 class="hero-title">Sew To Suit</h1>
    <p class="hero-tagline">Clothes made specially for you and designed by you.</p>
    <a class="read-more" href="#">READ MORE &raquo;</a>
  </div>
  <svg class="notch hero-notch" width="37" height="36" viewBox="0 0 37 36"><path d="M0 18 L37 0 L37 36 Z" fill="#59585a"/></svg>
</section>

<section class="process">
  <div class="process-panel">
    <ul class="steps">
      <li class="step"><h2>Be Inspired</h2><p>Be inspired by the latest trends, iconic styles from all eras<br>and the most prestigious fashion shows</p></li>
      <li class="step"><h2>Design</h2><p>Learn about our unique process,&nbsp; where you<br>become the designer</p></li>
      <li class="step"><h2>Choose the Fabric</h2><p>First rate fabrics &amp; highest<br>quality materials</p></li>
      <li class="step short"><h2>See your Creation</h2><p>See your creation in 3D</p></li>
      <li class="step"><h2>Wear it</h2><p>Wear your design, fitted for your exact body<br>measurements</p></li>
      <li class="step short"><h2>Have Fun, Be Creative</h2><p>The thrilling experience of creating</p></li>
    </ul>
  </div>
  <div class="photo process-photo" role="img" aria-label="Sepia fashion photo of a couple in a tailored dress and a dinner suit"></div>
  <svg class="notch process-notch" width="37" height="34" viewBox="0 0 37 34"><path d="M0 0 L37 17 L0 34 Z" fill="#59585a"/></svg>
</section>

<svg class="edge edge-bottom" viewBox="0 0 965 6"><rect width="965" height="6" fill="url(#saw-down)"/></svg>

<footer class="site-footer">
  <div class="footer-brand">
    <span class="brand-mark"></span>
    <span class="brand-name">Sew To Suit</span>
  </div>
  <nav class="footer-nav">
    <a href="#">HOME</a>
    <a href="#">WHAT IS SEW TO SUIT?</a>
    <a href="#">MORE</a>
  </nav>
  <ul class="contact">
    <li>
      <svg width="9" height="12" viewBox="0 0 9 12"><path d="M4.5 0 A4.5 4.5 0 0 1 9 4.5 C9 7.5 4.5 12 4.5 12 C4.5 12 0 7.5 0 4.5 A4.5 4.5 0 0 1 4.5 0 Z M4.5 2.6 A1.9 1.9 0 1 0 4.5 6.4 A1.9 1.9 0 1 0 4.5 2.6 Z" fill-rule="evenodd"/></svg>
      Fairhaven, CA
    </li>
    <li>
      <svg width="12" height="12" viewBox="0 0 12 12"><path d="M2.5 0.5 L4.5 3 L3.3 4.6 C4 6 5.8 7.9 7.4 8.7 L9 7.5 L11.5 9.5 L10 11.5 C5 11 1 7 0.5 2 Z"/></svg>
      1-555-010-2030
    </li>
    <li>
      <svg width="16" height="11" viewBox="0 0 16 11"><rect x="0" y="0" width="16" height="11" rx="1"/><path d="M0.5 0.8 L8 6.5 L15.5 0.8" fill="none" stroke="#000" stroke-width="1.2"/></svg>
      Sew To Suit @example.net
    </li>
  </ul>
  <div class="footer-rule"></div>
  <p class="copyright">@ 2015 Sew To Suit . All rights are reserved.</p>
  <div class="social" aria-label="Social links">
    <span></span><span></span><span></span><span></span>
  </div>
</footer>
</body>
</html>
```